Modern Business Card for Larkwell 2018

Our company assumes the best about people. We are creating an online community of entrepreneurs and business leaders who struggle with marketing their business online.

This business card should POP! We recently got a new logo and are launching a new website next month, so our business cards should make a statement that feels:
-Fresh
-Smart
-Trustworthy
-Fun

Target Market(s)

small business owners, entrepreneurs

Industry/Entity Type

Digital Marketing

Contact Information for Business Card

Dimensions: 3.5" x 2"

Font styles to use
Sans Serif

Colors
f37122
ffffff

Requirements
Must have
• We need a business card with a modern, bold design. We will use one side of the card as a lead-generation offer, so text on one side will need to fit up to 140 characters. The business card should stick to our core colors (orange, black, and white).
Nice to have
• We think a vertical "portrait" design could be interesting.
Should not have
• Should not look like a traditional business card. The round icon should stand out from a distance.

```html
<!DOCTYPE html>
<html lang="en">
<head>
<meta charset="utf-8">
<title>Larkwell Business Card</title>
<link href="https://fonts.googleapis.com/css2?family=Barlow:wght@400;500;700;800&family=Permanent+Marker&family=Noto+Serif:ital,wght@1,700&display=swap" rel="stylesheet">
<style>
  :root {
    --orange: #f37122;
    --white: #ffffff;
    --charcoal: #343233;
    --ink: #2f2d2e;
    --backdrop: #d9d9d9;
  }
  * { margin: 0; padding: 0; box-sizing: border-box; }
  html, body { width: 1200px; height: 1200px; overflow: hidden; }
  body {
    background: var(--backdrop);
    position: relative;
    font-family: "Barlow", sans-serif;
  }
  .card {
    position: absolute;
    top: 219px;
    width: 423px;
    height: 761px;
    overflow: hidden;
    box-shadow: 0 6px 24px rgba(0,0,0,0.25);
  }
  .card--front { left: 134px; }
  .card--back { left: 643px; }
  .card__top {
    height: 381px;
    display: flex;
    flex-direction: column;
    align-items: center;
    justify-content: center;
    gap: 14px;
  }
  .card--front .card__top { background: var(--white); }
  .card--back .card__top { background: var(--orange); }
  .brand-dot {
    width: 250px;
    height: 250px;
    border-radius: 50%;
  }
  .card--front .brand-dot { background: var(--orange); }
  .card--back .brand-dot { background: var(--white); }
  .brand-name {
    font-family: "Barlow", sans-serif;
    font-weight: 800;
    font-size: 30px;
    letter-spacing: 1px;
    line-height: 1;
  }
  .card--front .brand-name { color: var(--orange); }
  .card--back .brand-name { color: var(--white); }
  .card__bottom {
    height: 380px;
    display: flex;
    flex-direction: column;
    align-items: center;
    text-align: center;
  }
  .card--front .card__bottom {
    background: var(--charcoal);
    color: var(--white);
    justify-content: center;
    padding-top: 10px;
  }
  .person-name {
    font-family: "Permanent Marker", cursive;
    font-size: 50px;
    line-height: 1.15;
    text-transform: uppercase;
    margin-bottom: 30px;
  }
  .person-role {
    font-weight: 500;
    font-size: 22px;
    letter-spacing: 0.3px;
  }
  .person-email {
    font-weight: 400;
    font-size: 25px;
    letter-spacing: 0.4px;
  }
  .card--back .card__bottom {
    background: var(--white);
    color: var(--ink);
    padding-top: 22px;
  }
  .wordmark {
    font-weight: 800;
    font-size: 64px;
    line-height: 1;
    letter-spacing: 1px;
    text-transform: uppercase;
  }
  .tagline {
    font-family: "Noto Serif", serif;
    font-style: italic;
    font-weight: 700;
    font-size: 21px;
    margin-top: 12px;
  }
  .divider {
    width: 207px;
    height: 3px;
    background: var(--orange);
    margin: 52px 0 46px;
  }
  .offer {
    font-weight: 500;
    font-size: 21px;
    line-height: 1.3;
  }
  .offer-url {
    font-weight: 500;
    font-size: 31px;
    letter-spacing: 0.6px;
    margin-top: 6px;
  }
</style>
</head>
<body>
  <section class="card card--front">
    <div class="card__top">
      <div class="brand-dot"></div>
      <div class="brand-name">Larkwell</div>
    </div>
    <div class="card__bottom">
      <p class="person-name">Maren<br>Holt</p>
      <p class="person-role">Story Marketing Coach</p>
      <p class="person-email">maren@larkwellnow.com</p>
    </div>
  </section>

  <section class="card card--back">
    <div class="card__top">
      <div class="brand-dot"></div>
      <div class="brand-name">Larkwell</div>
    </div>
    <div class="card__bottom">
      <h1 class="wordmark">Larkwell</h1>
      <p class="tagline">Share Stories That Spark Growth</p>
      <div class="divider"></div>
      <p class="offer">Claim your free Larkwell Launch Kit and<br>our story marketing workbook now at</p>
      <p class="offer-url">larkwellnow.com/start</p>
    </div>
  </section>
</body>
</html>
```